Real Estate business card for me

Business card for a realtor. I have just a few "must haves"... so I am hoping to get some great ideas back without my telling you what I want.

I just want something cool, appealing to the eye, modern-ish while still looking clean and professional. I'm a young-spirited 40 yo man. I don't wan the business card of a 23 year old or a 63 year old! haha

Industry/Entity Type

Real Estate Agent

Contact Information for Business Card

Whatever Wexford Calloway logo you use, it should be true WC purple color. Outside of that, color scheme is open to ideas.

Requirements
Must have
• Must include:
• Wexford Calloway, Pemberly Estates
• Dale Fenwick
• REALTORĀ®
• 555.417.2093
• HomesWithDale@mailbox-demo.com
Nice to have
• Can include my picture, but it doesn't have to. I saw a card the other day with a house sketch on the backside saying "Your referrals are the sincerest compliment I can receive". That was cool. I also saw a card which one side was just a full frame picture of me, info on reverse side. I like all those ideas as well, but definitely open to ANYTHING cool, a little different, stands out from the monotony of business cards realtors are passing around. It needs to have a Wexford logo on it somewhere, but I don't want it huge or the focal point. Im selling me, not the franchise. You can literally google Wexford Calloway Home Services and find all of the logos. Any of the main stream ones will work. They are typically a dark purple or dark purple and cream.
Should not have
• I do not want a huge logo presence.

```html
<!DOCTYPE html>
<html lang="en">
<head>
<meta charset="utf-8">
<title>Dale Fenwick – Realtor Business Card</title>
<link href="https://fonts.googleapis.com/css2?family=Montserrat:wght@600;800&family=Roboto+Slab:wght@400&family=Lato:wght@400&family=Libre+Baskerville&display=swap" rel="stylesheet">
<style>
  :root {
    --backdrop: #7b4a26;
    --brand-red: #b01312;
    --card-white: #ffffff;
    --ink: #1d1d1d;
    --photo-dark: #333132;
    --photo-mid: #4a4446;
  }
  html, body {
    margin: 0;
    padding: 0;
    width: 1200px;
    height: 900px;
    overflow: hidden;
    background: var(--backdrop);
  }
  .canvas {
    position: relative;
    width: 1200px;
    height: 900px;
  }
  .card {
    position: absolute;
    box-shadow: 2px 3px 4px rgba(0, 0, 0, 0.45);
  }
  /* Front */
  .card-front {
    left: 330px;
    top: 90px;
    width: 555px;
    height: 343px;
    background: var(--brand-red);
  }
  .portrait {
    position: absolute;
    left: 24px;
    top: 34px;
    width: 264px;
    height: 265px;
    border-radius: 22px;
    background: radial-gradient(ellipse at 50% 45%, var(--photo-mid), var(--photo-dark) 70%);
  }
  .front-identity {
    position: absolute;
    left: 310px;
    top: 96px;
    width: 224px;
    text-align: center;
    color: var(--card-white);
  }
  .monogram {
    font-family: "Montserrat", sans-serif;
    font-weight: 800;
    line-height: 1;
    letter-spacing: 2px;
  }
  .front-identity .monogram {
    font-size: 84px;
  }
  .agent-name {
    margin-top: 18px;
    font-family: "Roboto Slab", serif;
    font-size: 26px;
    line-height: 1;
    letter-spacing: 0.3px;
  }
  .agent-title {
    display: flex;
    align-items: center;
    gap: 8px;
    margin-top: 10px;
    font-family: "Montserrat", sans-serif;
    font-weight: 600;
    font-size: 12px;
    letter-spacing: 0.5px;
  }
  .agent-title::before,
  .agent-title::after {
    content: "";
    flex: 1;
    height: 1px;
    background: var(--card-white);
  }
  /* Back */
  .card-back {
    left: 330px;
    top: 469px;
    width: 558px;
    height: 344px;
    background: var(--card-white);
  }
  .card-back .monogram {
    position: absolute;
    left: 0;
    right: 0;
    top: 70px;
    text-align: center;
    font-size: 84px;
    color: var(--brand-red);
  }
  .contact {
    position: absolute;
    left: 0;
    right: 0;
    top: 174px;
    text-align: center;
    font-family: "Lato", sans-serif;
    font-size: 18px;
    line-height: 23px;
    color: var(--ink);
  }
  .brokerage-band {
    position: absolute;
    left: 0;
    bottom: 0;
    width: 100%;
    height: 101px;
    background: var(--brand-red);
    color: var(--card-white);
    text-align: center;
    font-family: "Libre Baskerville", serif;
  }
  .brokerage-mark {
    display: block;
    margin: 10px auto 4px;
  }
  .brokerage-name {
    font-size: 13px;
    line-height: 14px;
    letter-spacing: 0.3px;
  }
  .brokerage-office {
    margin-top: 5px;
    font-size: 11px;
  }
</style>
</head>
<body>
<main class="canvas">
  <section class="card card-front">
    <div class="portrait" role="img" aria-label="Portrait photo of Dale Fenwick in a dark suit against a charcoal backdrop"></div>
    <div class="front-identity">
      <div class="monogram">DF</div>
      <div class="agent-name">Dale Fenwick</div>
      <div class="agent-title">REALTOR®</div>
    </div>
  </section>

  <section class="card card-back">
    <div class="monogram">DF</div>
    <div class="contact">
      <div class="contact-phone">555.417.2093</div>
      <div class="contact-email">HomesWithDale@mailbox-demo.com</div>
    </div>
    <div class="brokerage-band">
      <svg class="brokerage-mark" width="20" height="20" viewBox="0 0 20 20" aria-hidden="true">
        <circle cx="10" cy="10" r="9" fill="none" stroke="#ffffff" stroke-width="1.2"/>
      </svg>
      <div class="brokerage-name">Wexford Calloway<br>Home Services</div>
      <div class="brokerage-office">Pemberly Estates</div>
    </div>
  </section>
</main>
</body>
</html>
```